Business Card Design for Varomir Facility Services

We are looking for a Business Card Design for the Company "Varomir Facility Services."
Front side:
- Company Logo (small)
- Company Name, address, pohone, website and personal data.
- white background, for text e.g. company colors (blue or green like in the logo)
Please use following data:
Company data:
Varomir Facility Services Kostelac
Birkenhaldweg 14
8999 Lindmatt
www.varomir-fs.ch
Person data:
Tarik Kostelac
Geschäftsführer
+41 76 519 47 83
info@varomir-fs.ch
Back side:
could be colored in blue or green
please use a big logo sing and some smaller icons to say what is all beeing offered in facility services, like cleaning, maintenance cleaning
industrial cleaning, caretaking, gardening, disposal. There is no need for everyone of the icons if there are similar or an icon is standing for more of them.
colors to use:
blue: HEX 246BB0
green: HEX 52B33E

```html
<!DOCTYPE html>
<html lang="de">
<head>
<meta charset="utf-8">
<title>Varomir Facility Services – Business Card</title>
<link rel="stylesheet" href="https://fonts.googleapis.com/css2?family=Source+Sans+3:wght@400;600&display=swap">
<style>
  :root {
    --blue: #246BB0;
    --green: #52B33E;
    --green-back: #5ABA48;
    --ink: #3d3d3d;
    --white: #ffffff;
    --page: #ffffff;
  }
  * { margin: 0; padding: 0; box-sizing: border-box; }
  html, body {
    width: 1200px; height: 960px; overflow: hidden;
    background: var(--page);
    font-family: "Source Sans 3", "Source Sans Pro", sans-serif;
  }
  .card {
    position: absolute; left: 286px; width: 629px; height: 360px;
    box-shadow: 0 1px 4px rgba(0,0,0,0.35);
    overflow: hidden;
  }
  .card--front { top: 109px; background: var(--white); }
  .card--back { top: 492px; background: var(--green-back); }

  .brand-name {
    position: absolute; font-weight: 600; white-space: nowrap; letter-spacing: 0.5px;
  }
  .card--front .brand-name {
    right: 22px; top: 46px; font-size: 22px; color: var(--blue);
  }
  .card--back .brand-name {
    left: 0; right: 0; text-align: center; top: 160px; font-size: 36px; color: var(--white);
  }

  .person-name {
    position: absolute; left: 35px; top: 154px;
    font-size: 24px; font-weight: 600; color: var(--ink);
  }
  .person-role {
    position: absolute; left: 35px; top: 184px;
    font-size: 19px; font-weight: 400; color: var(--green);
  }
  .role-rule {
    position: absolute; left: 179px; right: 0; top: 196px;
    height: 2px; background: var(--green);
  }
  .contact-list { position: absolute; left: 35px; top: 218px; list-style: none; }
  .contact-list li {
    display: flex; align-items: center; height: 26.3px;
    font-size: 17px; color: var(--ink);
  }
  .contact-list svg { width: 17px; height: 17px; margin-right: 14px; flex: none; }

  .band { position: absolute; left: 0; bottom: 0; width: 629px; height: 23px; }

  .services {
    position: absolute; left: 0; top: 266px; width: 629px; height: 52px;
  }
  .service {
    position: absolute; display: flex; align-items: center;
    font-size: 18px; color: var(--white); white-space: nowrap;
  }
  .service svg { width: 15px; height: 15px; margin-right: 15px; }
</style>
</head>
<body>

<section class="card card--front" aria-label="Visitenkarte Vorderseite">
  <div class="brand-name">Varomir Facility Services</div>

  <h1 class="person-name">Tarik Kostelac</h1>
  <p class="person-role">Geschäftsführer</p>
  <div class="role-rule"></div>

  <ul class="contact-list">
    <li>
      <svg viewBox="0 0 24 24" aria-hidden="true"><path fill="#246BB0" d="M6.6 10.8a15 15 0 0 0 6.6 6.6l2.2-2.2c.3-.3.7-.4 1-.2 1.1.4 2.3.6 3.6.6.6 0 1 .4 1 1V20c0 .6-.4 1-1 1A17 17 0 0 1 3 4c0-.6.4-1 1-1h3.5c.6 0 1 .4 1 1 0 1.3.2 2.5.6 3.6.1.3 0 .7-.2 1z"/></svg>
      +41 76 519 47 83
    </li>
    <li>
      <svg viewBox="0 0 24 24" aria-hidden="true"><rect x="2" y="5" width="20" height="14" fill="#246BB0"/><path d="M2 5l10 8 10-8M2 19l7.5-7M22 19l-7.5-7" stroke="#fff" stroke-width="1.5" fill="none"/></svg>
      info@varomir-fs.ch
    </li>
    <li>
      <svg viewBox="0 0 24 24" aria-hidden="true"><circle cx="12" cy="12" r="9.5" fill="none" stroke="#246BB0" stroke-width="2"/><path fill="#246BB0" d="M7 6l4 2-1 4-4-1zM13 13l5 1-2 5-3-2zM14 4l4 3-3 2z"/></svg>
      www.varomir-fs.ch
    </li>
    <li>
      <svg viewBox="0 0 24 24" aria-hidden="true"><path fill="#246BB0" d="M12 2a5.5 5.5 0 0 0-5.5 5.5c0 4 5.5 9.5 5.5 9.5s5.5-5.5 5.5-9.5A5.5 5.5 0 0 0 12 2zm0 7.5a2 2 0 1 1 0-4 2 2 0 0 1 0 4z"/><ellipse cx="12" cy="20" rx="8" ry="2.2" fill="none" stroke="#246BB0" stroke-width="1.5"/></svg>
      Birkenhaldweg 14, 8999 Lindmatt
    </li>
  </ul>

  <svg class="band" viewBox="0 0 629 23" aria-hidden="true">
    <polygon points="0,0 413,0 401,23 0,23" fill="var(--blue)"/>
    <polygon points="420,0 629,0 629,23 408,23" fill="var(--green)"/>
  </svg>
</section>

<section class="card card--back" aria-label="Visitenkarte Rückseite">
  <div class="brand-name">Varomir Facility Services</div>

  <div class="services">
    <div class="service" style="left:40px;top:0">
      <svg viewBox="0 0 20 20" aria-hidden="true"><path fill="#fff" d="M10 0l1.6 8.4L20 10l-8.4 1.6L10 20l-1.6-8.4L0 10l8.4-1.6z"/></svg>Like cleaning</div>
    <div class="service" style="left:40px;top:26px">
      <svg viewBox="0 0 20 20" aria-hidden="true"><path fill="#fff" d="M10 0l1.6 8.4L20 10l-8.4 1.6L10 20l-1.6-8.4L0 10l8.4-1.6z"/></svg>Maintenance cleaning</div>
    <div class="service" style="left:274px;top:0">
      <svg viewBox="0 0 20 20" aria-hidden="true"><path fill="#fff" d="M10 0l1.6 8.4L20 10l-8.4 1.6L10 20l-1.6-8.4L0 10l8.4-1.6z"/></svg>Industrial cleaning</div>
    <div class="service" style="left:274px;top:26px">
      <svg viewBox="0 0 20 20" aria-hidden="true"><path fill="#fff" d="M10 0l1.6 8.4L20 10l-8.4 1.6L10 20l-1.6-8.4L0 10l8.4-1.6z"/></svg>Caretaking</div>
    <div class="service" style="left:485px;top:0">
      <svg viewBox="0 0 20 20" aria-hidden="true"><path fill="#fff" d="M10 0l1.6 8.4L20 10l-8.4 1.6L10 20l-1.6-8.4L0 10l8.4-1.6z"/></svg>Gardening</div>
    <div class="service" style="left:485px;top:26px">
      <svg viewBox="0 0 20 20" aria-hidden="true"><path fill="#fff" d="M10 0l1.6 8.4L20 10l-8.4 1.6L10 20l-1.6-8.4L0 10l8.4-1.6z"/></svg>Disposal</div>
  </div>

  <svg class="band" viewBox="0 0 629 23" aria-hidden="true">
    <rect width="629" height="23" fill="var(--white)"/>
    <polygon points="410,0 420,0 408,23 398,23" fill="var(--green-back)"/>
  </svg>
</section>

</body>
</html>
```